A business card design for a dental office. We have Two doctors working here. We practice general de

I already have a logo designed for the office with the name and a slogan.
Now I need to create design for a business card using the same logo.
Details Needed on the front side of the card are :
Bernard K. Oswin, DDS
Gerald M Fenwick, DDS
418 Birch Lane
Larkfield, NV 00000
Phone : 555 019 4831
Fax : 555 019 4832
Website : WWW.BrightmoorToothHaven.Com
Office hours by appointment
On the back side of the card need :
Appointment
Date....................Time...................
With....................................
If unable to keep your appointment, please give 24-48 hours notice in order to avoid broken appointment fee.

Industry/Entity Type

Dental Clinic

Contact Information for Business Card

Bernard K. Oswin, DDS
Gerald M Fenwick, DDS
418 Birch Lane
Larkfield, NV 00000
Phone : 555 019 4831
Fax : 555 019 4832
Appointment

Requirements
Must have
• Keep the Name and slogan on the logo on the front of the card. You can move them around the Logo and Name/Slogan of business (Oswin Family Dentistry/We give you reasons to smile) as you wish to get a feel of the design.
• Bernard K. Oswin, DDS
• Gerald M Fenwick, DDS
• 418 Birch Lane
• Larkfield, NV 00000
• Phone : 555 019 4831
• Fax : 555 019 4832
• WWW.BrightmoorToothHaven.Com
• Keep these three groups above as they are together now in different areas of the front side.
• On the back side of the card need :
• Appointment
• Date....................Time...................
• With....................................
• If unable to keep your appointment, please give 24-48 hours notice in order to avoid broken appointment fee.

```html
<!DOCTYPE html>
<html lang="en">
<head>
<meta charset="utf-8">
<title>Oswin Family Dentistry – Business Card</title>
<link href="https://fonts.googleapis.com/css2?family=Arimo:wght@700&family=Carlito:wght@400;700&display=swap" rel="stylesheet">
<style>
  :root {
    --page: #ecebea;
    --card: #ffffff;
    --brand-blue: #1f4f9c;
    --brand-red: #e0262d;
    --teal: #1aa285;
    --panel-top: #aed0ec;
    --panel-bottom: #0a56a6;
    --faint: #f1f1f1;
    --mark: #2a6fb5;
  }
  * { box-sizing: border-box; margin: 0; padding: 0; }
  html, body { width: 1200px; height: 900px; overflow: hidden; }
  body {
    position: relative;
    background: var(--page);
    font-family: "Carlito", "Calibri", sans-serif;
  }
  .card {
    position: absolute;
    background: var(--card);
    overflow: hidden;
    box-shadow: 0 3px 10px rgba(0,0,0,.15);
  }
  .card-front { left: 238px; top: 60px; width: 557px; height: 345px; }
  .card-back  { left: 457px; top: 518px; width: 560px; height: 344px; }

  .brand-name {
    font-family: "Arimo", "Arial", sans-serif;
    color: var(--brand-blue); font-weight: 700; letter-spacing: 1.6px;
  }

  /* front */
  .card-front .brand-name {
    position: absolute; left: 0; right: 0; top: 18px;
    text-align: center; font-size: 21px;
  }
  .slogan {
    position: absolute;
    display: flex; justify-content: center; align-items: center; gap: 8px;
    font-family: "Arimo", "Arial", sans-serif; font-weight: 400;
    color: var(--brand-red); font-size: 10px; letter-spacing: 1.4px;
    text-transform: uppercase;
  }
  .slogan::before, .slogan::after {
    content: ""; width: 44px; height: 1px; background: var(--brand-red);
  }
  .card-front .slogan { left: 0; right: 0; top: 44px; }
  .bridge-art {
    position: absolute; left: 0; right: 0; top: 64px; height: 132px;
    background: linear-gradient(180deg, #ffffff 0%, #e6f5f1 55%, #c9ebe2 100%);
  }
  .waterline {
    position: absolute; left: 0; right: 0; top: 196px; height: 8px;
    background: var(--teal);
    border-bottom: 2px solid #ffffff;
  }
  .info-panel {
    position: absolute; left: 0; right: 0; top: 204px; bottom: 0;
    background: linear-gradient(180deg, var(--panel-top) 0%, #4f8fcb 45%, var(--panel-bottom) 100%);
    color: #ffffff;
  }
  .doctors {
    position: absolute; right: 309px; top: 21px;
    text-align: right; font-weight: 700; font-size: 17.5px; line-height: 26px;
  }
  .contacts { position: absolute; left: 266px; top: 13px; list-style: none; font-size: 16px; line-height: 20px; }
  .contacts li { display: flex; align-items: center; gap: 8px; }
  .contacts svg { width: 12px; height: 12px; fill: #ffffff; }
  .hours {
    position: absolute; left: 0; right: 0; top: 80px;
    text-align: center; font-size: 16px;
  }
  .address {
    position: absolute; left: 0; right: 0; top: 104px;
    display: flex; align-items: center; gap: 8px; font-size: 16px;
  }
  .address::before, .address::after {
    content: ""; flex: 1; height: 1px; background: rgba(255,255,255,.8);
  }

  /* back */
  .backdrop-shape {
    position: absolute; left: 300px; top: -40px; width: 420px; height: 420px;
    border-radius: 50%; background: var(--faint);
  }
  .brand-mark {
    position: absolute; left: 44px; top: 30px; width: 110px; height: 110px;
    border-radius: 50%; background: var(--mark);
  }
  .card-back .brand-name {
    position: absolute; left: 183px; top: 70px; font-size: 19.5px;
  }
  .card-back .slogan { left: 183px; right: 42px; top: 100px; font-size: 9.5px; }
  .appointment-title {
    position: absolute; left: 0; right: 0; top: 146px;
    text-align: center; color: var(--brand-red); font-weight: 700; font-size: 22px;
  }
  .field { position: absolute; display: flex; align-items: baseline; gap: 12px; }
  .field .label { color: var(--brand-red); font-weight: 700; font-size: 18px; }
  .field .blank { display: block; height: 0; border-bottom: 2px dotted var(--teal); }
  .field-date { left: 84px; top: 190px; }
  .field-time { left: 274px; top: 190px; }
  .field-with { left: 84px; top: 241px; }
  .notice {
    position: absolute; left: 0; right: 0; top: 283px;
    text-align: center; font-weight: 700; font-size: 16.5px; line-height: 21px;
  }
  .notice .warn { color: var(--brand-red); display: block; }
  .notice .tail { color: var(--teal); display: block; }
</style>
</head>
<body>

<section class="card card-front">
  <h1 class="brand-name">OSWIN FAMILY DENTISTRY</h1>
  <p class="slogan">We give you reasons to smile</p>
  <div class="bridge-art" role="img" aria-label="Illustration of a teal arched steel bridge spanning the card"></div>
  <div class="waterline"></div>
  <div class="info-panel">
    <div class="doctors">
      <p>Bernard K. Oswin, DDS</p>
      <p>Gerald M Fenwick, DDS</p>
    </div>
    <ul class="contacts">
      <li><svg viewBox="0 0 24 24" aria-hidden="true"><path d="M6.6 10.8a15.1 15.1 0 0 0 6.6 6.6l2.2-2.2c.3-.3.7-.4 1-.2 1.1.4 2.3.6 3.6.6.6 0 1 .4 1 1V20c0 .6-.4 1-1 1A17 17 0 0 1 3 4c0-.6.4-1 1-1h3.5c.6 0 1 .4 1 1 0 1.3.2 2.5.6 3.6.1.3 0 .7-.2 1z"/></svg>555 019 4831</li>
      <li><svg viewBox="0 0 24 24" aria-hidden="true"><path d="M7 2h10v5H7zM4 8h16a2 2 0 0 1 2 2v8h-4v4H6v-4H2v-8a2 2 0 0 1 2-2zm4 8v4h8v-4z"/></svg>555 019 4832</li>
      <li><svg viewBox="0 0 24 24" aria-hidden="true"><path d="M12 2a10 10 0 1 0 0 20 10 10 0 0 0 0-20zm6.9 6h-3a15.6 15.6 0 0 0-1.3-3.9A8 8 0 0 1 18.9 8zM12 4c.8 1.2 1.5 2.5 1.9 4h-3.8c.4-1.5 1.1-2.8 1.9-4zM4.3 14a8 8 0 0 1 0-4h3.4a16 16 0 0 0 0 4zm.8 2h3a15.6 15.6 0 0 0 1.3 3.9A8 8 0 0 1 5.1 16zm3-8h-3a8 8 0 0 1 4.3-3.9C7.8 5.3 7.4 6.6 8.1 8zM12 20c-.8-1.2-1.5-2.5-1.9-4h3.8c-.4 1.5-1.1 2.8-1.9 4zm2.3-6H9.7a14 14 0 0 1 0-4h4.6a14 14 0 0 1 0 4zm.3 5.9c.6-1.2 1-2.5 1.3-3.9h3a8 8 0 0 1-4.3 3.9zm1.7-5.9a16 16 0 0 0 0-4h3.4a8 8 0 0 1 0 4z"/></svg>WWW.BrightmoorToothHaven.Com</li>
    </ul>
    <p class="hours">Office hours by appointment</p>
    <p class="address">418 Birch Lane Larkfield, NV 00000</p>
  </div>
</section>

<section class="card card-back">
  <div class="backdrop-shape"></div>
  <span class="brand-mark"></span>
  <span class="brand-name">OSWIN FAMILY DENTISTRY</span>
  <p class="slogan">We give you reasons to smile</p>
  <h2 class="appointment-title">Appointment</h2>
  <div class="field field-date"><span class="label">Date</span><span class="blank" style="width:124px"></span></div>
  <div class="field field-time"><span class="label">Time</span><span class="blank" style="width:146px"></span></div>
  <div class="field field-with"><span class="label">With</span><span class="blank" style="width:338px"></span></div>
  <p class="notice">
    <span class="warn">If unable to keep your appointment, please give 24-48 hours</span>
    <span class="tail">notice in order to avoid broken appointment fee.</span>
  </p>
</section>

</body>
</html>
```